School Poster

Design so that these can be placed in classrooms across the school.

Attached is another design we have had done. Use a similar theme.

Consider using themes from https://corvalhs.edq.example.au/

please edit Binder1 doc.

Students and teachers

```html
<!DOCTYPE html>
<html lang="en">
<head>
<meta charset="utf-8">
<title>Before You Ask the Teacher – Corval State High School</title>
<link rel="stylesheet" href="https://fonts.googleapis.com/css2?family=Fira+Sans:wght@600;700;800&family=Fira+Sans+Condensed:wght@600;700&family=Oswald:wght@300;400&display=swap">
<style>
  :root{
    --navy:#1b4282;
    --navy-deep:#1d3263;
    --ink:#1b3f80;
    --yellow:#f9e06b;
    --white:#ffffff;
    --footer:#1f1f1f;
    --placeholder-dark:#2c5598;
    --placeholder-light:#dfe7f4;
  }
  *{margin:0;padding:0;box-sizing:border-box}
  html,body{width:849px;height:1200px;overflow:hidden;background:var(--white)}
  .poster{position:relative;width:849px;height:1200px;overflow:hidden;
    background:linear-gradient(115deg,var(--navy) 0%,var(--navy-deep) 100%);
    font-family:"Fira Sans",sans-serif;color:var(--ink)}
  .poster__lower{position:absolute;left:0;top:0;width:849px;height:1200px}

  .school-mark{position:absolute;left:37px;top:60px;width:172px;text-align:center;color:var(--white)}
  .school-mark__dot{width:82px;height:82px;border-radius:50%;background:var(--yellow);margin:0 auto 14px}
  .school-mark__name{font-family:"Fira Sans",sans-serif;font-weight:700;font-size:19px;line-height:1.2}

  .headline{position:absolute;left:233px;top:40px;color:var(--white);font-weight:800;
    font-size:73px;line-height:66px;letter-spacing:-1px;text-transform:uppercase}
  .subhead{position:absolute;left:236px;top:186px;color:var(--yellow);
    font-family:"Fira Sans Condensed",sans-serif;font-weight:600;font-size:54px;line-height:1;letter-spacing:-0.5px}

  .step{position:absolute;top:302px;width:213px;height:640px}
  .step--think{left:57px}
  .step--check{left:319px}
  .step--ask{left:583px}
  .step__frame{position:absolute;left:0;top:0;width:213px;height:170px;
    border:3px solid var(--yellow);border-bottom:none;border-radius:10px 10px 0 0}
  .step__number{position:absolute;left:-26px;top:-6px;width:62px;height:62px;border-radius:50%;
    background:var(--white);border:7px solid var(--navy);color:var(--navy-deep);
    font-family:"Fira Sans Condensed",sans-serif;font-weight:700;font-size:32px;line-height:48px;text-align:center}
  .step__icon{position:absolute;left:50px;top:22px;width:113px;height:113px;border-radius:12px;background:var(--placeholder-dark)}
  .step__label{position:absolute;left:-4px;top:151px;width:221px;height:79px;background:var(--yellow);
    border:5px solid var(--navy);border-radius:12px;display:flex;align-items:center;justify-content:center;
    text-align:center;font-family:"Fira Sans Condensed",sans-serif;font-weight:700;font-size:28px;line-height:27px;
    color:var(--navy);letter-spacing:-0.8px;text-transform:uppercase}
  .step__body{position:absolute;left:0;top:226px;width:213px;height:414px;background:var(--white);
    border:3px solid var(--navy);border-top:none;border-radius:0 0 12px 12px;padding:17px 8px 0 14px}
  .step__lead{font-weight:700;font-size:21px;line-height:25px;text-align:center;margin-bottom:24px;padding-right:6px}
  .step__list{list-style:none}
  .step__list li{position:relative;padding-left:19px;font-weight:600;font-size:18px;line-height:22px;margin-bottom:22px}
  .step__list li::before{content:"";position:absolute;left:0;top:7px;width:10px;height:10px;border-radius:50%;background:var(--yellow)}
  .step--check .step__list li{margin-bottom:22px}
  .step--ask .step__lead{margin-bottom:14px}
  .step--ask .step__list li{margin-bottom:19px}
  .step__close{font-weight:600;font-size:18px;line-height:22px;margin-top:-2px}

  .value{position:absolute;top:957px;width:194px}
  .value--believe{left:73px}
  .value--strive{left:329px}
  .value--achieve{left:593px}
  .value__art{width:112px;height:94px;margin:0 auto;border-radius:10px;background:var(--placeholder-light)}
  .value__badge{margin-top:13px;height:48px;border-radius:12px;background:var(--navy);color:var(--white);
    font-family:"Fira Sans Condensed",sans-serif;font-weight:700;font-size:31px;line-height:48px;text-align:center;letter-spacing:-0.5px}
  .value-arrow{position:absolute;top:1078px;width:40px;height:18px}
  .value-arrow--one{left:281px}
  .value-arrow--two{left:542px}

  .references{position:absolute;left:0;top:1148px;width:849px;height:52px;background:var(--footer);
    color:var(--white);font-family:"Oswald",sans-serif;font-weight:300;font-size:10.2px;line-height:19px;padding:6px 0 0 37px;white-space:nowrap}
</style>
</head>
<body>
<main class="poster">
  <svg class="poster__lower" viewBox="0 0 849 1200" aria-hidden="true">
    <path d="M0 730 Q 424 612 849 730 L849 1200 L0 1200 Z" fill="#ffffff"/>
  </svg>

  <div class="school-mark">
    <div class="school-mark__dot"></div>
    <div class="school-mark__name">Corval State High School</div>
  </div>

  <h1 class="headline">Before you ask<br>the teacher…</h1>
  <p class="subhead">TRY THESE STEPS FIRST!</p>

  <section class="step step--think">
    <div class="step__frame"></div>
    <div class="step__number">1</div>
    <div class="step__icon" role="img" aria-label="Line icon of a head with a glowing brain"></div>
    <h2 class="step__label">Think<br>first</h2>
    <div class="step__body">
      <p class="step__lead">Don't give up straight away.</p>
      <ul class="step__list">
        <li>Read the question carefully.</li>
        <li>Identify what you already know.</li>
        <li>Try a strategy you've used before.</li>
        <li>Give yourself thinking time.</li>
      </ul>
    </div>
  </section>

  <section class="step step--check">
    <div class="step__frame"></div>
    <div class="step__number">2</div>
    <div class="step__icon" role="img" aria-label="Line icon of a checklist clipboard with a magnifying glass"></div>
    <h2 class="step__label">Check your<br>supports</h2>
    <div class="step__body">
      <p class="step__lead">Before asking for help, check</p>
      <ul class="step__list">
        <li>Learning goal and success criteria.</li>
        <li>Worked examples.</li>
        <li>Class notes.</li>
        <li>Classroom displays.</li>
        <li>StudyHub resources.</li>
        <li>Task sheet and instructions.</li>
      </ul>
    </div>
  </section>

  <section class="step step--ask">
    <div class="step__frame"></div>
    <div class="step__number">3</div>
    <div class="step__icon" role="img" aria-label="Line icon of three people beneath a speech bubble"></div>
    <h2 class="step__label">Ask 3 before<br>me</h2>
    <div class="step__body">
      <p class="step__lead">Ask three sources before asking the teacher:</p>
      <ul class="step__list">
        <li>A person (partner or neighbour)</li>
        <li>A place (notes, display, StudyHub)</li>
        <li>A resource (worked example, task sheet)</li>
      </ul>
      <p class="step__close">Then ask the teacher if you still need help.</p>
    </div>
  </section>

  <div class="value value--believe">
    <div class="value__art" role="img" aria-label="Line illustration of two students standing together"></div>
    <div class="value__badge">WE BELIEVE</div>
  </div>
  <svg class="value-arrow value-arrow--one" viewBox="0 0 40 18" aria-hidden="true">
    <path d="M2 2 L12 2 L20 9 L12 16 L2 16 L10 9 Z M19 2 L29 2 L37 9 L29 16 L19 16 L27 9 Z" fill="#1b4282"/>
  </svg>
  <div class="value value--strive">
    <div class="value__art" role="img" aria-label="Line illustration of two students climbing a mountain"></div>
    <div class="value__badge">WE STRIVE</div>
  </div>
  <svg class="value-arrow value-arrow--two" viewBox="0 0 40 18" aria-hidden="true">
    <path d="M2 2 L12 2 L20 9 L12 16 L2 16 L10 9 Z M19 2 L29 2 L37 9 L29 16 L19 16 L27 9 Z" fill="#1b4282"/>
  </svg>
  <div class="value value--achieve">
    <div class="value__art" role="img" aria-label="Line illustration of two students raising a flag on a summit"></div>
    <div class="value__badge">WE ACHIEVE</div>
  </div>

  <footer class="references">
    <p>Harlowe, M. (2025). "Why Students Don't Ask for Help - And How to Change That." Downloaded on 24/04/2026 from https://www.learnwell.example.org/article/asking-for-help/</p>
    <p>ELRO. (2024). "Supporting Self-Regulated Learning." Downloaded on 24/04/2026 from https://www.edevidence.example.au/files/2024-02/self-regulated-learning.pdf</p>
  </footer>
</main>
</body>
</html>
```